Commercial Real Estate

We need a business card design for a new commercial real estate business that specializes in apartment building brokerage. Not individual units but the entire complex. We find and represent the owners existing buildings and well as new buyers for those buildings. The design should convey trust, integrity, knowledge and growth. It should be easily read.

Target Market(s)

40 to 65 years old

Industry/Entity Type

Real Estate

```html
<!DOCTYPE html>
<html lang="en">
<head>
<meta charset="utf-8">
<title>Northvale Property Investments – Business Card</title>
<link href="https://fonts.googleapis.com/css2?family=Open+Sans:wght@400;600;700&display=swap" rel="stylesheet">
<style>
  :root {
    --backdrop: #ecebe8;
    --card: #ffffff;
    --teal: #5cbcbc;
    --teal-light: #8fd6d4;
    --teal-deep: #2f9696;
    --slate: #3f4a4c;
    --ink: #2c3335;
    --muted: #7b8486;
    --on-teal: #ffffff;
  }
  * { box-sizing: border-box; margin: 0; padding: 0; }
  html, body {
    width: 1200px; height: 913px; overflow: hidden;
    background: var(--backdrop);
    font-family: "Open Sans", Arial, sans-serif;
  }
  .stage {
    width: 1200px; height: 913px;
    display: flex; align-items: center; justify-content: center; gap: 40px;
  }
  .card {
    position: relative;
    width: 540px; height: 309px;
    background: var(--card);
    border-radius: 4px;
    box-shadow: 0 6px 18px rgba(0,0,0,0.12);
    overflow: hidden;
  }
  .brand {
    position: absolute;
    display: flex; align-items: center; gap: 10px;
  }
  .brand-mark {
    width: 14px; height: 14px; flex: none;
    background: var(--teal);
  }
  .brand-name {
    font-weight: 700;
    color: var(--slate);
    letter-spacing: 0.03em;
    line-height: 1.2;
  }
  .card-front .brand {
    left: 50%; top: 50%;
    transform: translate(-50%, -50%);
    white-space: nowrap;
  }
  .card-front .brand-name { font-size: 24px; }
  .card-back .brand { left: 40px; top: 200px; max-width: 230px; }
  .card-back .brand-name { font-size: 19px; }
  .swoosh { position: absolute; inset: 0; }
  .holder {
    position: absolute; right: 28px; top: 18px; text-align: right;
  }
  .holder-name { font-size: 17px; font-weight: 700; color: var(--ink); }
  .holder-role { font-size: 11px; color: var(--muted); margin-top: -2px; }
  .contact {
    position: absolute; right: 20px; top: 128px;
    list-style: none; text-align: right;
    color: var(--on-teal); font-size: 10.5px; line-height: 1.55;
  }
  .contact li { display: flex; justify-content: flex-end; align-items: flex-start; gap: 7px; }
  .contact svg { width: 11px; height: 11px; flex: none; margin-top: 3px; }
</style>
</head>
<body>
<main class="stage">

  <section class="card card-front" aria-label="Card front">
    <div class="brand">
      <span class="brand-mark"></span>
      <span class="brand-name">Northvale Property Investments</span>
    </div>
  </section>

  <section class="card card-back" aria-label="Card back">
    <svg class="swoosh" viewBox="0 0 540 309" aria-hidden="true">
      <defs>
        <linearGradient id="tealFill" x1="0" y1="0" x2="1" y2="1">
          <stop offset="0" stop-color="#8fd6d4"/>
          <stop offset="0.6" stop-color="#5cbcbc"/>
          <stop offset="1" stop-color="#2f9696"/>
        </linearGradient>
      </defs>
      <path d="M540 75 C410 78 350 110 335 185 C322 245 275 292 160 309 L540 309 Z" fill="url(#tealFill)"/>
      <path d="M540 62 C400 66 338 98 322 178 C307 240 262 286 140 309" fill="none" stroke="#3f4a4c" stroke-width="7"/>
    </svg>

    <div class="holder">
      <div class="holder-name">Your Name</div>
      <div class="holder-role">owner</div>
    </div>

    <ul class="contact">
      <li>00000000000
        <svg viewBox="0 0 12 12"><path d="M2 1h3l1 3-2 1a7 7 0 0 0 3 3l1-2 3 1v3c-6 0-10-4-10-10z" fill="currentColor"/></svg></li>
      <li>www.website.com
        <svg viewBox="0 0 12 12"><circle cx="6" cy="6" r="5" fill="none" stroke="currentColor"/><path d="M1 6h10M6 1c-3 3-3 7 0 10M6 1c3 3 3 7 0 10" fill="none" stroke="currentColor" stroke-width="0.8"/></svg></li>
      <li>yourname@website.com
        <svg viewBox="0 0 12 12"><rect x="1" y="2.5" width="10" height="7" fill="currentColor"/><path d="M1 2.5l5 4 5-4" fill="none" stroke="#5cbcbc" stroke-width="0.9"/></svg></li>
      <li>Your commercial address in<br>just two line
        <svg viewBox="0 0 12 12"><path d="M6 11C3 7 2 5.5 2 4.2a4 4 0 0 1 8 0C10 5.5 9 7 6 11z" fill="currentColor"/><circle cx="6" cy="4.3" r="1.4" fill="#5cbcbc"/></svg></li>
    </ul>

    <div class="brand">
      <span class="brand-mark"></span>
      <span class="brand-name">Northvale Property Investments</span>
    </div>
  </section>

</main>
</body>
</html>
```